Illustrated cover for unique non-fiction book (paperback & eBook)

I know the image I want on my book covers (eBook and paperback) but I need you to come up with the style and treatment. I am a self-publisher and my book is about the human obsession with being better than animals, even though scientists keep telling us there’s no evidence to support it. To illustrate how illogical it is I want to show a see-saw. On the end that is down (left) sits a man, and on the end that is up (right) sits a whole bunch of large and small animals that should outweigh him but don’t. Birds on heads and shoulders etc. Title: 'Why We Crown Ourselves Above Beasts'; author’s name: Derek Moffatbright. The style should be modern, uncluttered and probably not too realistic (I don’t want a cartoon style since the content of the book is pretty serious). No strong colour preferences at this stage, just needs to be eye-catching with good contrast. Perhaps a plain white background might work. Dimensions: 215 x 135mm, 374 pages, imprint: Pellmoor Press. Back page text is attached. [NOTE: If you feel you could express this illogicality in a completely different way please feel free to submit a draft design.]

Target Market(s)

General readers, particularly those interested in social sciences/life sciences.

Industry/Entity Type

Publishing

Requirements
Must have
• Good impact, clearly showing the absurdity of our attitude towards other species.
Nice to have
• Suggestthat the book is interesting and challenging.
Should not have
• Not cluttered or difficult to readthe image.

```html
<!DOCTYPE html>
<html lang="en">
<head>
<meta charset="utf-8">
<title>Why We Crown Ourselves Above Beasts — Cover Wrap</title>
<link href="https://fonts.googleapis.com/css2?family=Marcellus&family=Marcellus+SC&family=EB+Garamond:ital,wght@0,400;0,500;1,400&display=swap" rel="stylesheet">
<style>
  :root {
    --page-bg: #e9e8e5;
    --slate: #3b3e45;
    --slate-deep: #2a2c31;
    --ink-black: #0d0d0f;
    --cream: #e9e4da;
    --cream-soft: #d9d3c7;
    --oxblood: #6c2a25;
    --ink: #1c1c1e;
    --art-light: #a59e92;
    --art-dark: #4a4742;
  }
  * { box-sizing: border-box; margin: 0; padding: 0; }
  html, body { width: 1200px; height: 800px; overflow: hidden; }
  body {
    background: var(--page-bg);
    font-family: "EB Garamond", Georgia, serif;
    color: var(--ink);
  }
  .cover-wrap {
    position: absolute;
    left: 138px; top: 60px;
    width: 924px; height: 680px;
    display: flex;
    box-shadow: 0 14px 40px rgba(0,0,0,0.18);
  }

  /* Back cover */
  .back-cover {
    position: relative;
    width: 427px; height: 100%;
    background: linear-gradient(180deg, var(--slate-deep) 0%, #1a1b1e 55%, var(--ink-black) 100%);
    color: var(--cream);
    padding: 56px 38px 0;
    text-align: center;
  }
  .back-title {
    font-family: "Marcellus SC", "Marcellus", serif;
    font-weight: 400;
    font-size: 24px;
    line-height: 1.15;
    letter-spacing: 0.5px;
  }
  .back-hook {
    margin: 26px 0 30px;
    background: var(--cream);
    color: var(--ink);
    padding: 12px 14px;
    font-style: italic;
    font-size: 13.2px;
    line-height: 1.5;
    text-align: justify;
  }
  .back-body p {
    font-size: 10.4px;
    line-height: 1.55;
    text-align: justify;
    text-align-last: center;
    margin-bottom: 14px;
    color: var(--cream-soft);
  }

  /* Spine */
  .spine {
    position: relative;
    width: 70px; height: 100%;
    background: var(--cream);
    border-left: 3px solid #55585f;
    border-right: 3px solid #55585f;
  }
  .spine-top {
    height: 250px;
    background: var(--slate);
    display: flex; justify-content: center; align-items: flex-start;
    padding-top: 24px;
  }
  .spine-imprint {
    writing-mode: vertical-rl;
    color: var(--cream);
    text-align: center;
  }
  .spine-imprint small {
    display: block;
    font-size: 8px;
    letter-spacing: 0.5px;
  }
  .spine-imprint span {
    font-family: "Marcellus SC", serif;
    font-size: 15px;
    letter-spacing: 1.5px;
  }
  .spine-title {
    writing-mode: vertical-rl;
    font-family: "Marcellus SC", serif;
    font-size: 17px;
    line-height: 1.05;
    letter-spacing: 0.5px;
    text-align: center;
    margin: 40px auto 0;
    color: var(--ink);
  }

  /* Front cover */
  .front-cover {
    position: relative;
    width: 427px; height: 100%;
    background: var(--cream);
    overflow: hidden;
  }
  .front-band {
    position: absolute; left: 0; top: 0;
    width: 100%; height: 270px;
    background: var(--slate);
  }
  .front-title {
    position: absolute; left: 60px; right: 26px; top: 64px;
    text-align: center;
    color: var(--cream);
    font-family: "Marcellus", serif;
    font-weight: 400;
  }
  .front-title .lead {
    display: block;
    font-size: 23px;
    letter-spacing: 0.5px;
  }
  .front-title .main {
    display: block;
    font-size: 78px;
    line-height: 0.95;
    letter-spacing: 1px;
    margin-top: 4px;
  }
  .front-title .boxed {
    display: inline-block;
    margin-top: 6px;
    background: var(--cream);
    color: var(--ink);
    font-size: 46px;
    line-height: 1;
    padding: 6px 18px 8px;
    letter-spacing: 1px;
  }
  .accent-rule {
    position: absolute; left: 30px; top: 82px;
    width: 7px; height: 470px;
    background: var(--oxblood);
  }
  .cover-art {
    position: absolute; left: 0; top: 0;
    width: 427px; height: 680px;
  }
  .subtitle {
    position: absolute; left: 58px; top: 318px;
    font-size: 20px;
    line-height: 1.3;
    color: var(--ink);
  }
  .subtitle em {
    font-style: normal;
    text-decoration: underline;
    text-decoration-color: var(--oxblood);
    text-underline-offset: 3px;
  }
  .author {
    position: absolute; left: 0; right: 0; bottom: 38px;
    text-align: center;
    font-family: "Marcellus SC", serif;
    font-size: 27px;
    letter-spacing: 1px;
    color: var(--ink);
  }
</style>
</head>
<body>
  <div class="cover-wrap">
    <section class="back-cover">
      <h2 class="back-title">Why We Crown Ourselves<br>Above Beasts</h2>
      <p class="back-hook">We have a paradox. Nowadays, we mistrust claims of supremacy relating to class, gender, race and nationality yet are happy to embrace human supremacy, the belief that our own species is inherently superior and set apart. Trouble is, scientists can’t find any evidence to support it. So why do we still insist on it?</p>
      <div class="back-body">
        <p>This is a Man’s-place-in-nature book for the modern age. The topic has long been a favourite, establishing the beliefs that shaped our view of ourselves over centuries. But those ideas were of their time. When we read them we cringe at the arrogance, the pomposity and the sheer sense of entitlement. They are light on objectivity and heavy on self-congratulation. It’s time to revisit the topic, this time aiming for simple honesty. Think how satisfying it will be to have an understanding of ourselves that we can finally trust.</p>
        <p>By joining this mind quest you will discover the reasons why humans seem so different. Not the promotional reasons, or the selective thinking, or the heroic myths, or the shared delusions, but the real reasons. The answers, fascinating but not always flattering, are waiting inside. It’s an investigation that will open a can of worms and reach a startling conclusion.</p>
        <p>After a career as a senior analyst in the IT sector, Derek Moffatbright applied his skills to the subject that had always struck him as illogical and full of dubious assumptions – man’s view of himself. A lifetime of interest in the social and natural sciences had taught him that the big picture is too often neglected as academics pursue their own avenues of research. So he set about integrating many of these fields of study in his own quest for understanding. The project was successful, uncovering a hidden and unexpected reality. It is this that he now wishes to share.</p>
      </div>
    </section>

    <section class="spine">
      <div class="spine-top">
        <div class="spine-imprint"><small>Published By</small><span>Pellmoor Press</span></div>
      </div>
      <div class="spine-title">Why We Crown Ourselves<br>Above Beasts</div>
    </section>

    <section class="front-cover">
      <div class="front-band"></div>
      <div class="accent-rule"></div>
      <h1 class="front-title">
        <span class="lead">WHY WE CROWN OURSELVES</span>
        <span class="main">ABOVE</span>
        <span class="boxed">BEASTS</span>
      </h1>
      <svg class="cover-art" viewBox="0 0 427 680" role="img" aria-label="Ink illustration of a see-saw: a seated man weighs down the left end while a heap of animals — elephant, hippos, snake, gorilla and a small bird — rides high on the right end">
        <defs>
          <linearGradient id="art-tone" x1="0" y1="0" x2="1" y2="1">
            <stop offset="0" stop-color="var(--art-light)"/>
            <stop offset="1" stop-color="var(--art-dark)"/>
          </linearGradient>
        </defs>
        <polygon points="212,286 410,286 410,586 60,586 60,412 212,412" fill="url(#art-tone)"/>
      </svg>
      <p class="subtitle">The <em>Real</em> Reasons<br>Why We Feel<br>Set Apart</p>
      <p class="author">Derek Moffatbright</p>
    </section>
  </div>
</body>
</html>
```